I need to make a car magnet

It needs to include the words "PLAVO TOUR" and "2026 MEMBER" as well as the attached silhouette of the golfer. The color scheme needs to be navy, red and white. The shape and dimensions are open for interpretation

```html
<!DOCTYPE html>
<html lang="en">
<head>
<meta charset="utf-8">
<title>PLAVO TOUR – Car Magnet</title>
<link rel="stylesheet" href="https://fonts.googleapis.com/css2?family=Exo+2:ital,wght@1,800;1,900&display=swap">
<style>
  :root {
    --page: #c9c9cb;
    --navy: #1c2a5c;
    --navy-light: #2c3f7f;
    --red: #e3262f;
    --white: #ffffff;
    --silhouette: #f2f2f4;
  }
  * { margin: 0; padding: 0; box-sizing: border-box; }
  html, body {
    width: 893px;
    height: 1200px;
    overflow: hidden;
    background: var(--page);
  }
  .canvas {
    position: relative;
    width: 893px;
    height: 1200px;
  }
  .magnet {
    position: absolute;
    left: 56px;
    top: 405px;
    width: 781px;
    height: 390px;
    background: radial-gradient(ellipse at 62% 45%, var(--navy-light) 0%, var(--navy) 65%);
    overflow: hidden;
    box-shadow: 0 4px 10px rgba(0,0,0,0.18);
  }
  .accent-panel {
    position: absolute;
    inset: 0;
    width: 100%;
    height: 100%;
  }
  .golfer-silhouette {
    position: absolute;
    left: 28px;
    top: 24px;
    width: 190px;
    height: 352px;
    border-radius: 70px 70px 10px 10px;
    background: linear-gradient(180deg, var(--silhouette), #dcdde2);
  }
  .headline {
    position: absolute;
    left: 230px;
    width: 530px;
    text-align: center;
    font-family: "Exo 2", sans-serif;
    font-style: italic;
    font-weight: 900;
    line-height: 1;
    letter-spacing: 2px;
  }
  .headline-top {
    top: 68px;
    font-size: 96px;
    color: var(--red);
  }
  .headline-bottom {
    top: 168px;
    font-size: 104px;
    color: var(--white);
  }
  .member-bar {
    position: absolute;
    left: 170px;
    right: 0;
    top: 296px;
    height: 48px;
    background: var(--red);
    display: flex;
    align-items: center;
    justify-content: center;
    padding-left: 60px;
  }
  .member-label {
    font-family: "Exo 2", sans-serif;
    font-style: italic;
    font-weight: 800;
    font-size: 32px;
    letter-spacing: 2px;
    color: var(--white);
  }
</style>
</head>
<body>
  <main class="canvas">
    <section class="magnet">
      <svg class="accent-panel" viewBox="0 0 781 390" preserveAspectRatio="none" aria-hidden="true">
        <polygon points="0,0 150,0 100,390 0,390" fill="var(--red)"/>
      </svg>
      <div class="golfer-silhouette" role="img" aria-label="White silhouette of a golfer putting"></div>
      <div class="headline headline-top">PLAVO</div>
      <div class="headline headline-bottom">TOUR</div>
      <div class="member-bar">
        <span class="member-label">2026 MEMBER</span>
      </div>
    </section>
  </main>
</body>
</html>
```